Vehicle Rental Hire in the Algarve - Portugal

We are opening a Vehicle Rental company in the Algarve - Portugal - this will attract both locals and Tourists visiting. So we want this website to capture the beautiful location we will be set in, along with the familiarity of a vehicle rental company. And to keep a colour scheme in Line with out Logo. We are Quenmira Vehicle Rental.

Industry/Entity Type

Vehicle Rental

Number of Pages Required

1 page

Requirements
Must have
• must be professional, and simple to use navigation bar - must also have a "make a reservation" box - similar to the screenshot attached - Under our logo it must read "Vehicle Rental"
Nice to have
• It needs to be in a colour scheme that fits in with our logo

```html
<!DOCTYPE html>
<html lang="en">
<head>
<meta charset="utf-8">
<title>Quenmira Vehicle Rental</title>
<link href="https://fonts.googleapis.com/css2?family=Fira+Sans+Condensed:wght@500;600;700&family=Lato:wght@400;700&family=Yellowtail&display=block" rel="stylesheet">
<style>
:root{
  --navy:#10108c;
  --blue:#1a1ad6;
  --red:#c4302b;
  --ink:#333;
  --muted:#555;
  --grey-bg:#ececec;
  --footer:#1f1f1f;
  --white:#fff;
}
*{box-sizing:border-box;margin:0;padding:0}
html,body{width:1200px;height:3100px;overflow:hidden}
body{position:relative;background:var(--white);font-family:"Lato",sans-serif;color:var(--ink)}
.abs{position:absolute}
.btn{position:absolute;background:var(--red);color:var(--white);font-family:"Fira Sans Condensed",sans-serif;font-weight:500;font-size:17px;display:flex;align-items:center;justify-content:center}
.heading{font-family:"Fira Sans Condensed",sans-serif;font-weight:700;color:var(--blue);font-size:56px;line-height:1;letter-spacing:.5px;white-space:nowrap}
.script{font-family:"Yellowtail",cursive;color:var(--red);font-size:48px;line-height:1;white-space:nowrap}

/* header */
.brand{left:110px;top:20px;display:flex;align-items:center;gap:8px}
.brand-mark{width:22px;height:22px;border:2px solid var(--blue);border-radius:50%}
.brand-name{font-family:"Fira Sans Condensed",sans-serif;font-weight:600;font-size:24px;color:var(--blue);line-height:1}
.brand-sub{left:140px;top:52px;font-size:13px;color:var(--red);font-weight:700}
.nav{left:460px;top:46px;display:flex;gap:27px;font-size:16px;color:#333}
.nav .active{color:var(--blue);font-weight:700}

/* hero */
.hero{left:0;top:111px;width:1200px;height:515px;background:linear-gradient(180deg,#8b9a8e 0%,#6f7a62 35%,#4f6a2e 70%,#8a8a3a 100%)}
.hero-title{left:112px;top:182px;font-family:"Fira Sans Condensed",sans-serif;font-weight:700;font-size:72px;line-height:76px;color:var(--white)}

/* reservation */
.reserve{left:686px;top:111px;width:403px;height:615px;background:var(--navy);color:var(--white);padding:28px 28px 0}
.reserve h2{font-family:"Fira Sans Condensed",sans-serif;font-weight:600;font-size:24px;text-align:center;margin-bottom:14px}
.reserve label{display:block;font-size:13.5px;margin-bottom:13px}
.field{background:var(--white);color:#666;font-size:13px;height:44px;display:flex;align-items:center;justify-content:space-between;padding:0 18px;margin-bottom:18px;margin-left:2px}
.field svg{width:10px;height:10px}
.check{display:flex;align-items:center;gap:10px;font-size:13.5px;margin:-2px 0 26px 2px}
.check span{width:17px;height:17px;background:#ddd;border-radius:3px}
.row{display:flex;gap:6px}
.row>div{flex:1}
.search{position:static;height:42px;margin:2px 0 0 2px}

/* about */
.about-photo{left:112px;top:850px;width:515px;height:372px;background:linear-gradient(135deg,#4b5b3b,#8c7a66 40%,#3a3a3a)}
.about-notch{left:560px;top:888px;width:80px;height:340px;background:var(--white)}
.about-text{left:606px;top:932px;width:480px}
.about-text h3{font-size:17.5px;font-weight:700;color:#222;margin-bottom:16px}
.about-text p{font-size:15px;line-height:28.5px;color:var(--muted);margin-bottom:6px}

/* airport */
.airport{left:0;top:1310px;width:1200px;height:454px;background:linear-gradient(90deg,#0f78c8 0%,#1aa0c8 40%,#c99a52 70%,#d9a45a 100%)}
.light{color:var(--white)}
.airport-sub{left:112px;top:1519px;font-size:17.5px;font-weight:700;color:var(--white)}
.airport-p{left:112px;top:1562px;width:490px;font-size:15px;line-height:28.5px;color:var(--white)}

/* testimonials */
.card{width:314px;height:306px;top:1992px;background:var(--white);box-shadow:0 0 6px rgba(0,0,0,.12);text-align:center;padding:26px 20px 0}
.quote{width:50px;height:50px;border-radius:50%;background:linear-gradient(135deg,#3a2fd0,#c4302b);margin:0 auto 28px;color:var(--white);font-family:Georgia,serif;font-size:42px;font-weight:700;line-height:62px}
.card p{font-size:15.5px;line-height:25px;color:#444}
.card h4{font-family:"Fira Sans Condensed",sans-serif;font-weight:500;font-size:17px;margin-top:10px;color:#222}
.stars{color:#f0a020;font-size:12px;letter-spacing:2px}
.arrow{width:40px;height:40px;border:1.5px solid #888;border-radius:50%;top:2126px;display:flex;align-items:center;justify-content:center}

/* newsletter */
.news{left:0;top:2378px;width:1200px;height:412px;background:var(--grey-bg)}
.news-p{left:0;top:2544px;width:1200px;text-align:center;font-size:15px;line-height:28.5px;color:#444}
.input{top:2633px;width:306px;height:51px;background:var(--white);border:1px solid #ddd;font-size:15px;color:#666;padding-left:22px;display:flex;align-items:center}

/* footer */
.footer{left:0;top:2790px;width:1200px;height:310px;background:var(--footer)}
.f-ring{left:138px;top:2843px;width:170px;height:170px;border:3px solid var(--white);border-radius:50%}
.f-name{left:110px;top:2900px;width:220px;text-align:center;font-family:"Fira Sans Condensed",sans-serif;font-weight:600;font-size:38px;color:var(--white);background:var(--footer);line-height:46px}
.socials{left:148px;top:3030px;display:flex;gap:7px}
.socials span{width:31px;height:31px;border:1.5px solid var(--white);border-radius:50%}
.f-col{color:var(--white)}
.f-col h5{font-family:"Fira Sans Condensed",sans-serif;font-weight:600;font-size:16px;margin-bottom:16px;letter-spacing:.3px;color:var(--white)}
.f-col a{display:block;font-size:15px;line-height:30px;color:var(--white);text-decoration:none}
.f-item{display:flex;gap:16px;font-size:15px;line-height:30px;margin-bottom:8px;color:var(--white)}
.f-item svg{width:15px;height:15px;margin-top:7px;flex:none}
.copy{left:0;top:3060px;width:1260px;text-align:center;font-size:15.5px;color:var(--white)}
</style>
</head>
<body>

<!-- header -->
<div class="abs brand"><span class="brand-mark"></span><span class="brand-name">QUENMIRA</span></div>
<div class="abs brand-sub">Vehicle Rental</div>
<nav class="abs nav"><span class="active">Home</span><span>Vehicle</span><span>Services</span><span>About</span><span>Contact</span><span>Reservations</span></nav>
<div class="btn" style="left:952px;top:35px;width:136px;height:41px">Explore</div>

<!-- hero -->
<div class="abs hero" role="img" aria-label="Black SUV with roof box on a road before green fields and mountains"></div>
<h1 class="abs hero-title">Quenmira<br>Vehicle Rental</h1>
<div class="btn" style="left:112px;top:344px;width:136px;height:41px">Learn More</div>

<form class="abs reserve">
  <h2>MAKE A RESERVATION</h2>
  <label>Pick up location</label>
  <div class="field">Please Choose... <svg viewBox="0 0 10 10"><path d="M2 3.5l3 3 3-3" fill="none" stroke="#222" stroke-width="1.6"/></svg></div>
  <div class="check"><span></span>Pick up location same as return location</div>
  <label>Driver's age</label>
  <div class="field">Please Choose... <svg viewBox="0 0 10 10"><path d="M2 3.5l3 3 3-3" fill="none" stroke="#222" stroke-width="1.6"/></svg></div>
  <label>Vehicle category</label>
  <div class="field">All <svg viewBox="0 0 10 10"><path d="M2 3.5l3 3 3-3" fill="none" stroke="#222" stroke-width="1.6"/></svg></div>
  <div class="row">
    <div><label>Pick up date</label><div class="field">dd-mm-aaaa</div></div>
    <div><label>Hour</label><div class="field">09:00 <svg viewBox="0 0 10 10"><path d="M2 3.5l3 3 3-3" fill="none" stroke="#222" stroke-width="1.6"/></svg></div></div>
  </div>
  <div class="row">
    <div><label>Drop off date</label><div class="field">dd-mm-aaaa</div></div>
    <div><label>Hour</label><div class="field">09:00 <svg viewBox="0 0 10 10"><path d="M2 3.5l3 3 3-3" fill="none" stroke="#222" stroke-width="1.6"/></svg></div></div>
  </div>
  <div class="btn search">Search</div>
</form>

<!-- about -->
<div class="abs heading" style="left:112px;top:735px">ABOUT US</div>
<div class="abs script" style="left:254px;top:768px">Abuot us</div>
<div class="abs about-photo" role="img" aria-label="Smiling couple and a dog inside a car on a road trip"></div>
<div class="abs about-notch"></div>
<div class="abs about-text">
  <h3>Lorem ipsum dolor sit amet, consectetur adipiscing elit</h3>
  <p>Lorem ipsum dolor sit amet, consectetur adipiscing elit, sed do eiusmod tempor incididunt ut labore et dolore magna aliqua. Ut enim ad minim veniam, quis nostrud exerci tation ullamco laboris nisi ut aliquip ex ea commodo consequat.</p>
  <p>Ut enim ad minim veniam, quis nostrud exerci tation ullamco laboris nisi ut aliquip ex eacoaute irure dolor in reprehen derit in voluptate velit.</p>
</div>
<div class="btn" style="left:606px;top:1163px;width:136px;height:41px">Learn More</div>

<!-- airport -->
<div class="abs airport" role="img" aria-label="Turquoise sea and golden cliffs over a sandy Algarve beach"></div>
<div class="abs heading light" style="left:112px;top:1403px">CAR HIRE AT AIRPORT</div>
<div class="abs script light" style="left:198px;top:1440px">Vehicle ready at your arrival</div>
<div class="abs airport-sub">Lorem ipsum dolor sit amet, consectetur adipiscing elit</div>
<p class="abs airport-p">Ut enim ad minim veniam, quis nostrud exerci tation ullamco laboris nisi ut aliquip ex eacoaute irure dolor in reprehen derit in voluptate velit.</p>
<div class="btn" style="left:112px;top:1648px;width:136px;height:41px">Learn More</div>

<!-- testimonials -->
<div class="abs heading" style="left:393px;top:1851px">TESTIMONIALS</div>
<div class="abs script" style="left:522px;top:1886px">What clients say</div>
<div class="abs arrow" style="left:36px"><svg width="14" height="14" viewBox="0 0 14 14"><path d="M9 2L4 7l5 5" fill="none" stroke="#777" stroke-width="1.5"/></svg></div>
<div class="abs arrow" style="left:1123px"><svg width="14" height="14" viewBox="0 0 14 14"><path d="M5 2l5 5-5 5" fill="none" stroke="#555" stroke-width="1.5"/></svg></div>
<div class="abs card" style="left:115px"><div class="quote">&#8221;</div><p>“ Sed ut perspiciatis unde omnis iste natus error sit voluptat accusantium doloremque laudantium, totam rem aperiam, eaque ipsa quae ab illo inventore veritatis et quasi architect”</p><h4>Maren T.</h4><div class="stars">★★★★★</div></div>
<div class="abs card" style="left:446px"><div class="quote">&#8221;</div><p>“ Sed ut perspiciatis unde omnis iste natus error sit voluptat accusantium doloremque laudantium, totam rem aperiam, eaque ipsa quae ab illo inventore veritatis et quasi architect”</p><h4>Maren T.</h4><div class="stars">★★★★★</div></div>
<div class="abs card" style="left:777px"><div class="quote">&#8221;</div><p>“ Sed ut perspiciatis unde omnis iste natus error sit voluptat accusantium doloremque laudantium, totam rem aperiam, eaque ipsa quae ab illo inventore veritatis et quasi architect”</p><h4>Maren T.</h4><div class="stars">★★★★★</div></div>

<!-- newsletter -->
<div class="abs news"></div>
<div class="abs heading" style="left:382px;top:2444px">NEWSLETTER</div>
<div class="abs script" style="left:505px;top:2480px">Subscribe to news</div>
<p class="abs news-p">Ut enim ad minim veniam, quis nostrud exerci tation ullamco laboris nisi<br>ut aliquip ex eacoaute irure dolor in reprehen derit in voluptate velit.</p>
<div class="abs input" style="left:288px">Full Name</div>
<div class="abs input" style="left:606px">Email</div>
<div class="btn" style="left:532px;top:2700px;width:136px;height:41px">Learn More</div>

<!-- footer -->
<div class="abs footer"></div>
<div class="abs f-ring"></div>
<div class="abs f-name">QUENMIRA</div>
<div class="abs socials"><span></span><span></span><span></span><span></span></div>
<div class="abs f-col" style="left:430px;top:2845px;width:290px">
  <h5>CONTACT</h5>
  <div class="f-item"><svg viewBox="0 0 15 15"><path d="M7.5 1a4.5 4.5 0 0 0-4.5 4.5c0 3.4 4.5 8.5 4.5 8.5s4.5-5.1 4.5-8.5A4.5 4.5 0 0 0 7.5 1zm0 6.3a1.8 1.8 0 1 1 0-3.6 1.8 1.8 0 0 1 0 3.6z" fill="#fff"/></svg><span>Quenmira Limitada,<br>Address comes here</span></div>
  <div class="f-item"><svg viewBox="0 0 15 15"><rect x="1" y="3" width="13" height="9" fill="#fff"/><path d="M1 3l6.5 5L14 3" fill="none" stroke="#1f1f1f" stroke-width="1.2"/></svg><span>info@quenmiralimitada.com</span></div>
  <div class="f-item"><svg viewBox="0 0 15 15"><path d="M3 1l3 3-1.5 2a8 8 0 0 0 4.5 4.5L11 9l3 3-2 2C6 14 1 9 1 3z" fill="#fff"/></svg><span>+1-555-014-2290</span></div>
</div>
<div class="abs f-col" style="left:750px;top:2845px">
  <h5>QUICK LINKS</h5>
  <a>Home</a><a>Vehicle</a><a>Services</a><a>About</a><a>Reservations</a>
</div>
<div class="abs f-col" style="left:956px;top:2845px">
  <h5>OTHER LINKS</h5>
  <a>Terms &amp; Conditions</a><a>Privacy Policy</a><a>Pricing</a><a>Contact</a>
</div>
<div class="abs copy">2024 Quenmira Limitada. All Rights Reserved.</div>

</body>
</html>
```